Small Business Directory Site Requires a Professional Responsive Web Design

Small Business Directory and Coupon Site - we require a complete website design for a brand new responsive & mobile friendly website. We already have a coder who will professional code our website in Magento.

All PSD pages need to be professionally designed then uploaded into a sharedrive (i.e. like filecrate). Additionally, as I cannot pre-empt everything, please note that we may require a little more assistance once the files have been transferred (for example, in www.brightlane-listings.example if you hover your mouse on the search box you will see a pop up box. We want one of these too and I think that means there may be extra design work here)

We have some draft page sketches have been created (there are some minor changes we want to the sketches provided though); however, we require an excellent designer to add the creative touches to it to make it look professionally created. All artwork/font must be legal.

-------------------------
We like the look of the www.brightlane-listings.example and www. marlowfolio.example

For the headers, please consider a font similar to RNS camellia. We likes this style, but it is too thin for the headers...so we need a variation like this one. For the copy/general text font, something basic that marries well with the headers.

---------------------

Please be sure to also read the brief we wrote for the coder as this will help with better understanding our design requirements.

In total I believe we have about 50 pages. This includes all the little pages and most of the pop up boxes (but not the little help key boxes). For example, pages include...

1. Login (this is where customers log in and can edit, manage their profiles. This means that there are backend membership pages)
2. Mini Services (same look and feel as the business coupons)
3. Resource Centre
4. Join (this is where customers learn about the packages available to submit a directory listing, if they ‘buy’ a package (i.e. free, $25 or $150 package) then they can create their own directory listing)
5. Search the directory (customer can view all the categories and also search the directory)
6. Create a directory listing (this is where customers learn about the packages available to submit a directory listing, if they ‘buy’ a package (i.e. free, $25 or $150 package) then they can create their own directory listing)
7. Quote finder (also know as Get a Quote)
8. Coupons (customer go to the business coupon page and can view all current coupons/submit a coupon)
9. Submit a coupon (form)
10.Advertise with us (form)
11. Join the forum
12.Submit an article or video (form)
13. Affiliates (listing of affiliates we currently have)
14. Become an affiliate (form)
15. Case studies (customer can view the case studies we have in the resource centre)
16. Help Guides (customer can view the help guides we have in the resource centre)
17. About Us
18 .Contact Us (form)
19. Terms & Condition
20. Privacy Policy
21. Supporting City Councils
22. Site Map
23. Forgot password / login details
24. Homepage
25. If we hover over a few areas (i.e. search box, location field) it pops up with more information.
etc etc etc. . . there are more pages.

Please see our filecrate link for the draft mock up pages that I have created so far.

https://www.cloudtrunk.example/sh/qk72pmw4rtz8nd/KLMvbTq2fWndxPzs8Yh4ecRQu

We are in a rush! We'd like to get the majority of the artwork completed by the end of the month. Minor fixes/tweaks can occur thereafter.

Target Market(s)

Small Businesses (employees 0 - 50) located throughout Australia

Industry/Entity Type

Business

Font styles to use
Sans Serif

Requirements
Must have
• Professional. Artwork must be legal (cannot be cut and paste or taken off other websites, must be legally purchased and used).Must look contemporary, fresh, modern.

Absolutely must be a responsive site!
Nice to have
• original work, original photos, original art.

like modern, fresh photos that demonstrate innovation, growth, small business, Australian scenery, stability, goals/passion.
Should not have
• cut and paste graphics, illegal graphics, not purchased graphics.

```html
<!DOCTYPE html>
<html lang="en">
<head>
<meta charset="utf-8">
<title>SB Assist Hub – Australia's Small Business Support</title>
<link rel="stylesheet" href="https://fonts.googleapis.com/css2?family=Ubuntu:wght@400;500;700&family=PT+Sans:wght@400;700&display=swap">
<style>
:root{
  --orange:#f7941d;
  --orange-text:#e8621a;
  --green:#3d9b1a;
  --green-dark:#2f7f12;
  --ink:#333;
  --muted:#555;
  --line:#d8d8d8;
  --band:#f2f2f2;
  --footer:#3b3b3b;
  --footer-text:#c9c9c9;
  --white:#fff;
}
*{box-sizing:border-box;margin:0;padding:0}
html,body{width:842px;height:1200px;overflow:hidden}
body{position:relative;background:var(--white);font-family:"PT Sans",sans-serif;color:var(--ink)}
.abs{position:absolute}
.heading{font-family:"Ubuntu",sans-serif}

/* header */
.site-header{left:0;top:0;width:842px;height:88px;border-bottom:1px solid var(--line)}
.brand{left:92px;top:30px;display:flex;align-items:center;gap:8px;font-family:"Ubuntu",sans-serif;font-size:21px;font-weight:500;color:var(--ink)}
.brand-mark{width:14px;height:14px;background:var(--orange)}
.search-panel{left:407px;top:14px;width:344px;height:56px;background:var(--orange);padding:16px 17px;display:flex;gap:9px}
.search-field{height:24px;background:var(--white);font-size:9px;font-style:italic;color:#999;display:flex;align-items:center;padding-left:10px;gap:5px}
.search-what{width:133px}
.search-where{width:133px}
.search-btn{width:22px;height:24px;background:#f05a1a;display:flex;align-items:center;justify-content:center}

.main-nav{left:92px;top:100px;display:flex;font-size:10px;color:var(--muted);font-family:"Ubuntu",sans-serif}
.main-nav span{padding:0 9px;border-left:1px solid #999;line-height:11px}
.main-nav span:first-child{border-left:0;padding-left:10px}

/* hero */
.hero{left:0;top:122px;width:842px;height:424px;background:radial-gradient(ellipse at 50% 40%,#f3a23a 0%,#c9772a 35%,#8a5a34 65%,#4d4038 100%)}
.hero-arrow{top:206px;width:35px;height:37px;background:rgba(40,40,40,.7);display:flex;align-items:center;justify-content:center}
.hero-title{left:0;width:842px;top:66px;text-align:center;color:var(--white);font-size:24px}
.hero-sub{left:238px;top:108px;width:366px;height:30px;background:rgba(70,60,50,.65);color:var(--white);font-size:20px;text-align:center;line-height:30px;white-space:nowrap}
.offer{left:235px;top:166px;width:373px;height:194px;background:rgba(90,75,60,.7)}
.offer-title{top:12px;left:0;width:373px;text-align:center;color:var(--white);font-size:21px;font-weight:700}
.offer-bar{left:20px;top:49px;width:335px;height:27px;background:#b5b2ad;color:var(--white);display:flex;align-items:center;padding:0 10px;gap:8px;font-size:14px}
.offer-bar small{font-size:10px}
.offer-card{left:20px;top:76px;width:335px;height:101px;background:var(--white);padding:12px 15px}
.offer-card h3{font-family:"Ubuntu",sans-serif;font-weight:400;color:var(--orange-text);font-size:14px;margin-bottom:10px}
.offer-card p{font-size:9px;line-height:17px;color:var(--muted)}
.checkout-btn{right:17px;bottom:12px;width:101px;height:22px;background:var(--orange);color:var(--white);font-family:"Ubuntu",sans-serif;font-size:10px;font-weight:500;display:flex;align-items:center;justify-content:center}

/* community */
.section-title{left:0;width:842px;top:593px;text-align:center;font-size:19px;color:var(--ink)}
.card{top:639px;width:203px;height:232px;border:1px solid var(--line);text-align:center;padding:13px}
.card-media{width:177px;height:98px}
.card h4{font-family:"Ubuntu",sans-serif;font-weight:400;color:var(--orange-text);font-size:11.5px;margin:17px 0 9px;white-space:nowrap}
.card p{font-size:9px;line-height:15.5px;color:var(--muted)}
.card p em{color:var(--green);font-style:italic}
.btn{display:inline-block;margin-top:14px;background:var(--green);color:var(--white);font-family:"Ubuntu",sans-serif;font-size:10px;padding:6px 14px;border-bottom:2px solid var(--green-dark)}
.partner-box{margin:3px auto 0;width:131px;height:56px;border:1px solid var(--line);display:flex;align-items:center;justify-content:center;font-family:"Ubuntu",sans-serif;font-size:16px;color:#1d3d6e}

/* partners */
.partners{left:0;top:912px;width:842px;height:105px;background:var(--band)}
.partner{top:19px;width:112px;height:66px;background:var(--white);border:1px solid var(--line);display:flex;align-items:center;justify-content:center;font-family:"Ubuntu",sans-serif;font-size:15px;font-weight:500;color:#2a2a2a}

/* footer */
.site-footer{left:0;top:1017px;width:842px;height:183px;background:var(--footer)}
.foot-col{top:27px}
.foot-col h5{font-family:"Ubuntu",sans-serif;font-weight:400;font-size:10px;color:var(--white);margin-bottom:12px;letter-spacing:.2px}
.foot-col li{list-style:none;font-size:8.5px;color:var(--footer-text);line-height:18.5px}
.foot-btn{display:inline-block;margin-top:6px;background:var(--green);color:var(--white);font-family:"Ubuntu",sans-serif;font-size:9.5px;padding:6px 9px}
.social{display:flex;gap:5px}
.social span{width:27px;height:27px;border:1.5px solid #aaa;border-radius:50%}
.copyright{left:620px;top:1121px;width:130px;text-align:right;font-size:9px;line-height:16px;color:var(--footer-text)}
</style>
</head>
<body>

<header class="site-header abs">
  <div class="brand abs"><span class="brand-mark"></span>SB Assist Hub</div>
  <form class="search-panel abs">
    <div class="search-field search-what">What are you looking for?</div>
    <div class="search-field search-where">
      <svg width="7" height="9" viewBox="0 0 7 9"><path d="M3.5 0A3.5 3.5 0 0 0 0 3.5C0 6 3.5 9 3.5 9S7 6 7 3.5A3.5 3.5 0 0 0 3.5 0z" fill="#999"/><circle cx="3.5" cy="3.5" r="1.3" fill="#fff"/></svg>
      Where ?
    </div>
    <div class="search-btn">
      <svg width="10" height="10" viewBox="0 0 10 10"><circle cx="4" cy="4" r="3" fill="none" stroke="#fff" stroke-width="1.6"/><path d="M6.3 6.3L9 9" stroke="#fff" stroke-width="1.8"/></svg>
    </div>
  </form>
</header>

<nav class="main-nav abs">
  <span>Login</span><span>Join</span><span>Coupons</span><span>Mini Services</span><span>Get a Quote</span><span>Advertise</span><span>Resource Centre</span>
</nav>

<section class="hero abs" role="img" aria-label="Photograph of a sunlit orange sandstone sea cave">
  <div class="hero-arrow abs" style="left:0">
    <svg width="8" height="10" viewBox="0 0 8 10"><path d="M6 1L2 5l4 4" fill="none" stroke="#fff" stroke-width="2"/></svg>
  </div>
  <div class="hero-arrow abs" style="right:0">
    <svg width="8" height="10" viewBox="0 0 8 10"><path d="M2 1l4 4-4 4" fill="none" stroke="#fff" stroke-width="2"/></svg>
  </div>
  <h1 class="hero-title heading abs" style="font-weight:400">Let Us Help You Grow</h1>
  <h2 class="hero-sub heading abs" style="font-weight:400">Australia’s Small Business Assist Hub</h2>
  <div class="offer abs">
    <h2 class="offer-title heading abs">Create A Directory Listing Today</h2>
    <div class="offer-bar abs heading">
      <svg width="11" height="10" viewBox="0 0 11 10"><rect x=".5" y="2" width="7.5" height="7.5" fill="none" stroke="#fff"/><path d="M2 5l2 2 6-6" fill="none" stroke="#fff" stroke-width="1.4"/></svg>
      <span>A$25/<small>YEAR</small></span>
      <svg style="margin-left:auto" width="16" height="8" viewBox="0 0 16 8"><path d="M4 0L0 4l4 4zM12 0l4 4-4 4z" fill="#fff"/></svg>
    </div>
    <div class="offer-card abs">
      <h3>3 Category Listing</h3>
      <p>Promote Your Special Offers Business Profile &amp; Logo Website &amp; Email Link money for your network.</p>
      <div class="checkout-btn abs">Checkout</div>
    </div>
  </div>
</section>

<h2 class="section-title heading abs" style="font-weight:400">Real Support from Our Community</h2>

<article class="card abs" style="left:92px">
  <div class="card-media" role="img" aria-label="Photo of two colleagues reviewing paperwork at a desk" style="background:linear-gradient(135deg,#c9d3dc,#8f9aa5 55%,#e3e6e8)"></div>
  <h4>How Did You Sort Your Business?</h4>
  <p>Learn from Dana Merrow, a real small busi-<br>ness owner. How she started <em>More &gt;&gt;</em></p>
  <span class="btn">Case Study</span>
</article>

<article class="card abs" style="left:320px">
  <div class="card-media" role="img" aria-label="Video still of a business owner at her computer" style="background:linear-gradient(135deg,#6e7683,#4a525d);display:flex;align-items:center;justify-content:center">
    <svg width="48" height="48" viewBox="0 0 48 48"><circle cx="24" cy="24" r="21" fill="rgba(0,0,0,.25)" stroke="#fff" stroke-width="3"/><path d="M19 14l14 10-14 10z" fill="#fff"/></svg>
  </div>
  <h4>Why Go with SB Assist Hub?</h4>
  <p>What small business owner can't relate to<br>the ongoing task of attracting. <em>More &gt;&gt;</em></p>
  <span class="btn" style="padding:6px 18px">Whiteboard video</span>
</article>

<article class="card abs" style="left:546px">
  <div class="partner-box">Harbor Cover</div>
  <h4 style="margin-top:26px">Become An Affiliate</h4>
  <p>If you have a network of small busi-<br>nesses, let us help to create additional<br>value for your members and make<br>money for your network. Talk to us today<br>about how we can help.</p>
</article>

<section class="partners abs">
  <div class="partner abs" style="left:102px">Grainfield</div>
  <div class="partner abs" style="left:233px">Deskline</div>
  <div class="partner abs" style="left:366px">Telvo</div>
  <div class="partner abs" style="left:497px">Harbor Cover</div>
  <div class="partner abs" style="left:628px">Coastair</div>
</section>

<footer class="site-footer abs">
  <div class="foot-col abs" style="left:92px">
    <h5>SITE DIRECTRY</h5>
    <ul><li>Search the Directry</li><li>Create a Directry Listing</li><li>Quote Finder</li><li>Coupons</li><li>Submit a Coupons</li><li>Advertise With Us</li></ul>
  </div>
  <div class="foot-col abs" style="left:232px">
    <h5>RESOURCES</h5>
    <ul style="margin-top:2px"><li>Join the Forum</li><li>Submit an Article</li><li>Affilated</li><li>Become An Affilated</li><li>Case Studies</li><li>Help Guides</li></ul>
  </div>
  <div class="foot-col abs" style="left:352px">
    <h5>POPULAR CATEGORIES</h5>
    <ul style="margin-top:1px"><li>Neque porro quisquam</li><li>Est qui dolorem</li><li>Ipsum quia dolor sit</li><li>Amet, consectetur,</li></ul>
    <span class="foot-btn">View All Categorie</span>
  </div>
  <div class="foot-col abs" style="left:507px">
    <h5>ABOUT</h5>
    <ul style="margin-top:1px"><li>About Us</li><li>Contact Us</li><li>Terms &amp; Conditions</li><li>Privacy Policy</li><li>Supporting council</li><li>Site Map</li></ul>
  </div>
  <div class="foot-col abs" style="left:630px">
    <h5>FOLLOW US</h5>
    <div class="social" aria-label="Social links"><span></span><span></span><span></span><span></span></div>
  </div>
</footer>
<p class="copyright abs">Copyright ©2014 Northsite.<br>All Right Reserved.</p>

</body>
</html>
```